New Flyer for a Revamped Brand!

Hearthwild Pantry's vision is to give our customers their lives back, so they can spend more time dancing in their living rooms! To live your best life you need your health and your time, and with Hearthwild Pantry's pre-packaged, totally healthy (no gluten, no grains, no sugar), meals delivered straight to your door you can spend your time living a life you love!

We have just celebrated our first birthday, and in line with our newly stated vision, we would like to create some new collateral that is in line with this - starting with flyers!

I have attached our logo, and some images of our meals. Our website is www.hearthwildpantry-example.com.au and our homepage outlines the what, how and why.

We are looking for a flyer that both describes what we do, and captures our vision for health, time, and happiness.

Reason: All of the designs seem to be coming back as A4, where as a flyer should be DL sized. Please amend to DL.

Target Market(s)

Used in a letterbox drop in high income areas, as well as to hand out at health and fitness events

Industry/Entity Type

Kitchen

Requirements
Must have
• E: info@hearthwildpantry-example.com.au
• W: www.hearthwildpantry-example.com.au
• P: 0491 562 317
• FB: facebook.com/hearthwildpantryoz
• Insta: instagram.com/hearthwildpantryoz

```html
<!DOCTYPE html>
<html lang="en">
<head>
<meta charset="utf-8">
<title>Hearthwild Pantry – DL Flyer Back</title>
<link rel="stylesheet" href="https://fonts.googleapis.com/css2?family=Amatic+SC:wght@400&display=swap">
<style>
  :root {
    --paper: #ffffff;
    --maroon: #4a000e;
    --saffron: #f29a1f;
    --trim-mark: #555555;
  }
  html, body {
    margin: 0;
    padding: 0;
    width: 1200px;
    height: 619px;
    overflow: hidden;
    background: var(--paper);
  }
  .flyer-sheet {
    position: relative;
    width: 1200px;
    height: 619px;
  }
  .crop-marks {
    position: absolute;
    inset: 0;
  }
  .flyer-panel {
    position: absolute;
    left: 40px;
    top: 40px;
    width: 1107px;
    height: 537px;
    background: var(--maroon);
  }
  .tagline {
    position: absolute;
    left: 0;
    right: 0;
    top: 267px;
    margin: 0;
    text-align: center;
    font-family: "Amatic SC", cursive;
    font-weight: 400;
    font-size: 88px;
    line-height: 1;
    letter-spacing: 2px;
    color: var(--saffron);
  }
</style>
</head>
<body>
  <main class="flyer-sheet">
    <svg class="crop-marks" width="1200" height="619" viewBox="0 0 1200 619" aria-hidden="true">
      <g stroke="var(--trim-mark)" stroke-width="1">
        <line x1="40.5" y1="0" x2="40.5" y2="27"/>
        <line x1="1147.5" y1="0" x2="1147.5" y2="27"/>
        <line x1="40.5" y1="592" x2="40.5" y2="619"/>
        <line x1="1147.5" y1="592" x2="1147.5" y2="619"/>
        <line x1="0" y1="40.5" x2="26" y2="40.5"/>
        <line x1="1160" y1="40.5" x2="1188" y2="40.5"/>
        <line x1="0" y1="577.5" x2="26" y2="577.5"/>
        <line x1="1160" y1="577.5" x2="1188" y2="577.5"/>
      </g>
    </svg>
    <section class="flyer-panel"></section>
    <h1 class="tagline">Nourish. Thrive. Repeat.</h1>
  </main>
</body>
</html>
```